Real Estate Company / Capital Needs Cards!

need business cards designed using the logos that were just designed by pixelbarn.

Reason: per designers request deadline extended 1 day…thank you.

Target Market(s)

Investors and clients looking to purchase real estate or invest in the business.

Industry/Entity Type

Business

Requirements
Must have
• two designs - one for the real estate logo and one for the capital logo, similar but slightly different.
Nice to have
• something to make it pop (perhaps on the back)
Should not have
• much color

```html
<!DOCTYPE html>
<html lang="en">
<head>
<meta charset="utf-8">
<title>Arden Real Estate – Business Cards</title>
<link rel="stylesheet" href="https://fonts.googleapis.com/css2?family=Cinzel:wght@400;600&display=swap">
<style>
  :root {
    --backdrop: #6b4a30;
    --card: #0a0a0a;
    --card-edge: #1c1c1c;
    --silver: #dcdcdc;
    --silver-soft: #bdbdbd;
    --ghost: #1f1f1f;
  }
  html, body {
    margin: 0;
    padding: 0;
    width: 1200px;
    height: 498px;
    overflow: hidden;
    background: var(--backdrop);
  }
  .canvas {
    position: relative;
    width: 1200px;
    height: 498px;
    font-family: "Cinzel", serif;
  }
  .card {
    position: absolute;
    top: 95px;
    width: 520px;
    height: 300px;
    background: var(--card);
    border: 1px solid var(--card-edge);
    border-radius: 30px;
    box-shadow: 0 12px 30px rgba(0,0,0,0.55);
    overflow: hidden;
    color: var(--silver);
  }
  .card--front { left: 50px; }
  .card--back  { left: 630px; }

  .ghost-mark {
    position: absolute;
    background: var(--ghost);
    border-radius: 22px;
  }
  .card--front .ghost-mark { right: 50px; top: 40px; width: 170px; height: 190px; }
  .card--back  .ghost-mark { left: 160px; top: 45px; width: 200px; height: 220px; }

  .brand {
    position: absolute;
    left: 30px;
    top: 68px;
    display: flex;
    align-items: center;
    gap: 10px;
  }
  .brand__square {
    width: 62px;
    height: 62px;
    background: var(--silver);
    border-radius: 6px;
  }
  .brand__name {
    font-size: 36px;
    line-height: 0.95;
    letter-spacing: 1px;
    color: var(--silver);
  }
  .brand__sub {
    font-size: 14px;
    letter-spacing: 2px;
    color: var(--silver);
  }

  .contact {
    position: absolute;
    left: 40px;
    top: 166px;
    line-height: 1.25;
  }
  .contact__name { font-size: 19px; margin-bottom: 6px; }
  .contact__line { font-size: 15px; color: var(--silver-soft); }
  .contact__address { font-size: 14px; color: var(--silver-soft); margin-top: 10px; }

  .back-title {
    position: absolute;
    left: 0;
    right: 0;
    top: 95px;
    text-align: center;
  }
  .back-title__name {
    font-size: 78px;
    letter-spacing: 4px;
    line-height: 1;
    color: var(--silver);
  }
  .back-title__sub {
    font-size: 31px;
    letter-spacing: 6px;
    font-weight: 600;
    color: var(--silver);
    margin-top: 4px;
    padding-left: 40px;
  }
</style>
</head>
<body>
<main class="canvas">
  <section class="card card--front" aria-label="Card front">
    <div class="ghost-mark" aria-hidden="true"></div>
    <div class="brand">
      <div class="brand__square" aria-hidden="true"></div>
      <div>
        <div class="brand__name">ARDEN</div>
        <div class="brand__sub">REAL ESTATE</div>
      </div>
    </div>
    <div class="contact">
      <div class="contact__name">Your Name, Title</div>
      <div class="contact__line">P: 123-456-7980</div>
      <div class="contact__line">F: 123-568-7896</div>
      <div class="contact__line">E: hello@ardenrealestate.com</div>
      <div class="contact__address">Street Name City Name State ZipCode</div>
    </div>
  </section>

  <section class="card card--back" aria-label="Card back">
    <div class="ghost-mark" aria-hidden="true"></div>
    <div class="back-title">
      <div class="back-title__name">ARDEN</div>
      <div class="back-title__sub">REAL ESTATE</div>
    </div>
  </section>
</main>
</body>
</html>
```